Electrical contractor Brochure design

We are looking a elegant brochure design for our new branding campaign. Logo ai file is attached. We mainly work in power plants and manufacturing facilities. We would like some pictures to show those types of facilities.

Target Market(s)

Industrial commercial electrician

Industry/Entity Type

Contractor

Font styles to use
Sans Serif

```html
<!DOCTYPE html>
<html lang="en">
<head>
<meta charset="utf-8">
<title>Kestrel Electric Brochure</title>
<link href="https://fonts.googleapis.com/css2?family=Lato:wght@400;700&family=Roboto:wght@400;500;900&display=swap" rel="stylesheet">
<style>
  :root {
    --red: #c8202b;
    --red-light: #dd3a44;
    --red-dark: #a3141d;
    --ink: #1e1e1e;
    --grey-text: #444;
    --paper: #ffffff;
    --backdrop: #e6e6e6;
  }
  * { box-sizing: border-box; margin: 0; padding: 0; }
  html, body { width: 1200px; height: 824px; overflow: hidden; }
  body {
    background: var(--backdrop);
    font-family: "Lato", sans-serif;
    position: relative;
  }
  .spread {
    position: absolute;
    left: 170px; top: 108px;
    width: 860px; height: 608px;
    display: flex;
    box-shadow: 0 6px 24px rgba(0,0,0,.18);
  }
  .page {
    position: relative;
    width: 430px; height: 608px;
    background: var(--paper);
    overflow: hidden;
  }

  /* Back cover */
  .back-photo {
    position: absolute; left: 0; top: 0; width: 430px; height: 360px;
    background: linear-gradient(180deg, #3a3a3a 0%, #6f6f6f 35%, #4c4c4c 60%, #161616 100%);
  }
  .back-band {
    position: absolute; left: 0; top: 0; width: 430px; height: 608px;
  }
  .mission {
    position: absolute; left: 24px; top: 352px; width: 384px; color: #fff;
  }
  .mission h2 {
    font-family: "Roboto", sans-serif; font-weight: 500; font-size: 22px; line-height: 26px; margin-bottom: 4px;
  }
  .mission p { font-size: 10px; line-height: 13.5px; }
  .contact {
    position: absolute; left: 24px; top: 528px; list-style: none; color: var(--ink);
  }
  .contact li { display: flex; align-items: center; gap: 8px; font-size: 10px; line-height: 14px; }
  .contact li.main { font-size: 14px; line-height: 18px; font-weight: 700; margin-left: 17px; }
  .contact svg { width: 9px; height: 9px; fill: var(--ink); }
  .back-brand {
    position: absolute; right: 26px; top: 494px;
    font-family: "Roboto", sans-serif; font-weight: 900; font-size: 16px; color: var(--ink);
    display: flex; align-items: center; gap: 6px;
  }
  .back-brand .dot { width: 10px; height: 10px; border-radius: 50%; background: var(--red); }

  /* Front cover */
  .front-title {
    position: absolute; left: 0; top: 0; width: 430px; height: 86px;
    background: linear-gradient(180deg, var(--red-light), var(--red));
    color: #fff; text-align: center; padding-top: 14px;
    font-family: "Roboto", sans-serif;
  }
  .front-title h1 { font-weight: 900; font-size: 40px; line-height: 1; letter-spacing: .5px; }
  .front-title span { display: block; font-weight: 500; font-size: 17px; letter-spacing: 1px; }
  .front-photo {
    position: absolute; left: 0; top: 86px; width: 430px; height: 230px;
    background: linear-gradient(180deg, #2a2f6e 0%, #3c3f86 40%, #8a6a40 72%, #1c1a18 100%);
  }
  .front-band {
    position: absolute; left: 0; top: 316px; width: 430px; height: 110px;
    background: linear-gradient(180deg, var(--red-dark), var(--red) 40%, var(--red-light));
    color: #fff; text-align: center; padding: 38px 30px 0;
    font-family: "Roboto", sans-serif; font-size: 10px; line-height: 1.3;
  }
  .front-brand {
    position: absolute; left: 0; top: 462px; width: 430px; text-align: center;
    font-family: "Roboto", sans-serif;
  }
  .front-brand .name {
    font-weight: 900; font-size: 24px; color: var(--ink);
    display: inline-flex; align-items: center; gap: 8px;
  }
  .front-brand .name .dot { width: 14px; height: 14px; border-radius: 50%; background: var(--red); }
  .front-brand .web { display: block; font-size: 10px; letter-spacing: 3px; color: var(--grey-text); margin-top: 8px; }
</style>
</head>
<body>
<main class="spread">
  <section class="page back-cover">
    <div class="back-photo" role="img" aria-label="Black and white photo of an industrial site at night with a tall crane and lights"></div>
    <svg class="back-band" viewBox="0 0 430 608" aria-hidden="true">
      <path d="M0 340 L430 300 L430 478 L0 520 Z" fill="var(--red)"/>
      <path d="M0 520 L430 478 L430 484 L0 526 Z" fill="var(--red-light)"/>
    </svg>
    <div class="mission">
      <h2>Our Mission</h2>
      <p>Kestrel Electric's mission is to be the premier provider of electrical contracting in the Ohio Valley and surrounding states. We will continuously strive to provide our clients with value added service by providing a safe, challenging, and rewarding environment for our team, which in turn motivates them to take pride in establishing a successful partnership with our many clients throughout our marketplace.</p>
    </div>
    <ul class="contact">
      <li class="main">555-014-2207</li>
      <li><svg viewBox="0 0 10 10"><path d="M2 1l2 2-1 1.5a6 6 0 0 0 2.5 2.5L7 6l2 2-1.5 1.5C4 9 1 6 .5 2.5z"/></svg>555-014-2208</li>
      <li><svg viewBox="0 0 10 10"><rect x="1" y="3" width="8" height="5"/></svg>info (@) kestrel-electric.com</li>
      <li><svg viewBox="0 0 10 10"><circle cx="5" cy="5" r="4"/></svg>www.kestrel-electric.com</li>
      <li><svg viewBox="0 0 10 10"><path d="M5 0a3.5 3.5 0 0 1 3.5 3.5C8.5 6 5 10 5 10S1.5 6 1.5 3.5A3.5 3.5 0 0 1 5 0z"/></svg>118 Ridgeline Ave, Harlow OH 45011</li>
    </ul>
    <div class="back-brand"><span class="dot"></span>Kestrel Electric</div>
  </section>

  <section class="page front-cover">
    <header class="front-title">
      <h1>ELECTRICAL</h1>
      <span>CONTRACTING SERVICE</span>
    </header>
    <div class="front-photo" role="img" aria-label="Power plant with tall smoking chimneys lit up at dusk"></div>
    <div class="front-band">
      <p>Lorem IpsumIt is a long established fact that a reader will be distracted by the readable content of a page when looking at its layout. The point of using Lorem Ipsum is that it has a more-or-less normal distribution</p>
    </div>
    <div class="front-brand">
      <span class="name"><span class="dot"></span>Kestrel Electric</span>
      <span class="web">www.kestrel-electric.com</span>
    </div>
  </section>
</main>
</body>
</html>
```